New Business Card Design Project

We require a business card design for Vexalund, a newly established Indian company.
Our focus is on the development, manufacturing, and export of a diverse array of pharmaceutical products on a global scale. The card should convey a professional appearance, as our primary markets are in Africa, China, and Southeast Asian nations.
We envision a two-sided business card, with the reverse side dedicated to a logo set against a solid color or an elegantly designed pattern. The corners should be rounded. We would appreciate seeing both horizontal and vertical design options. We trust the designer to utilize their expertise in creating this design.

The content for the business card is included in the attached Word file.

Target Market(s)

Our primary markets are in Africa, China, and Southeast Asian, Latin America, Maldives, Sri Lanka

Industry/Entity Type

Pharmaceutical Manufacturing and Export

Contact Information for Business Card

Colors

Designer to choose colors to be used in the design.

Requirements
Must have
• The reverse side of the business card features solely the logo along with the tagline, "Care in Every Dose."
Should not have
• The logo should not exceed two instances, encompassing both the front and back sides of the card.

```html
<!DOCTYPE html>
<html lang="en">
<head>
<meta charset="utf-8">
<title>Vexalund Business Card</title>
<link rel="stylesheet" href="https://fonts.googleapis.com/css2?family=Poppins:wght@400;500;600&display=swap">
<style>
  :root {
    --canvas-bg: #2b2b2d;
    --brand-blue: #29a8e0;
    --brand-coral: #f0604c;
    --card-white: #ffffff;
    --text-grey: #3a3a3a;
    --tagline-white: #ffffff;
    --emboss-light: #c9f1ff;
  }
  * { box-sizing: border-box; margin: 0; padding: 0; }
  html, body {
    width: 1200px; height: 874px; overflow: hidden;
    background: var(--canvas-bg);
    font-family: "Poppins", sans-serif;
  }
  .canvas {
    position: relative; width: 1200px; height: 874px;
    display: flex; flex-direction: column; align-items: center; justify-content: center; gap: 30px;
  }
  .card {
    position: relative; width: 700px; height: 400px;
    border-radius: 24px; overflow: hidden;
  }
  /* Reverse side */
  .card--back {
    background: var(--brand-blue);
    display: flex; flex-direction: column; align-items: center; justify-content: flex-end;
    padding-bottom: 110px;
  }
  .back-mark { display: flex; align-items: center; gap: 14px; }
  .back-mark__dot { width: 20px; height: 20px; border-radius: 50%; background: var(--emboss-light); }
  .back-mark__name {
    font-weight: 600; font-size: 64px; letter-spacing: 1px; color: var(--emboss-light); line-height: 1;
  }
  .back-tagline {
    margin-top: 30px; font-weight: 400; font-size: 15px; color: var(--tagline-white);
  }
  /* Front side */
  .card--front { background: var(--card-white); }
  .front-shapes { position: absolute; inset: 0; width: 100%; height: 100%; }
  .front-content {
    position: absolute; left: 0; right: 0; top: 60px;
    display: flex; flex-direction: column; align-items: center; text-align: center;
  }
  .front-mark { display: flex; align-items: center; gap: 10px; }
  .front-mark__dot { width: 14px; height: 14px; border-radius: 50%; background: var(--brand-coral); }
  .front-mark__name { font-weight: 600; font-size: 44px; color: var(--brand-blue); line-height: 1.1; }
  .person-name { margin-top: 12px; font-weight: 600; font-size: 27px; color: var(--brand-blue); line-height: 1.1; }
  .person-role { font-weight: 400; font-size: 14px; color: var(--brand-coral); margin-top: 2px; }
  .address { margin-top: 14px; font-size: 15px; color: var(--text-grey); line-height: 1.4; }
  .contact-line { margin-top: 12px; font-size: 15px; color: var(--text-grey); line-height: 1.4; }
  .contact-line .sep { padding: 0 8px; }
</style>
</head>
<body>
<main class="canvas">
  <section class="card card--back" aria-label="Card reverse">
    <div class="back-mark">
      <span class="back-mark__dot"></span>
      <span class="back-mark__name">Vexalund</span>
    </div>
    <p class="back-tagline">Care in Every Dose</p>
  </section>

  <section class="card card--front" aria-label="Card front">
    <svg class="front-shapes" viewBox="0 0 700 400" preserveAspectRatio="none" aria-hidden="true">
      <path d="M0 0 L150 0 L245 170 Q262 205 225 222 L0 340 Z" fill="var(--brand-coral)"/>
      <path d="M700 20 L700 400 L615 400 L520 250 Q500 215 540 196 Z" fill="var(--brand-blue)"/>
    </svg>
    <div class="front-content">
      <div class="front-mark">
        <span class="front-mark__dot"></span>
        <span class="front-mark__name">Vexalund</span>
      </div>
      <p class="person-name">Arjun K. Mehra</p>
      <p class="person-role">CEO</p>
      <p class="address">12, Nilgiri Nagar, Wardha<br>442001, India</p>
      <p class="contact-line">+919800012345<span class="sep">|</span>amehra@vexalund.com<br>www.vexalund.com</p>
    </div>
  </section>
</main>
</body>
</html>
```